Business Card for brovaLINK

Create a Business Card with an existing logo for brovaLINK AG. We are a Information Technology company that does consulting and developing SW to automate business processes. The main colors are given from the logo.

Industry/Entity Type

Business

Requirements
Nice to have
• we use a a font style Century Gothic in our documents

```html
<!DOCTYPE html>
<html lang="en">
<head>
<meta charset="utf-8">
<title>brovaLINK business card</title>
<link rel="stylesheet" href="https://fonts.googleapis.com/css2?family=Questrial&family=Cormorant+SC:wght@600&display=swap">
<style>
  :root {
    --stage-centre: #2ba300;
    --stage-edge: #1c6e00;
    --card-dark: #0d0d0d;
    --card-dark-mid: #1c1c1c;
    --card-light: #ffffff;
    --ink: #3a3a3a;
    --ink-soft: #222222;
    --brand-green: #2f9e1e;
    --band-green: #56ad2c;
    --brand-blue: #2b8fd6;
  }
  html, body {
    margin: 0;
    width: 1200px;
    height: 1200px;
    overflow: hidden;
  }
  body {
    position: relative;
    background: radial-gradient(circle at 50% 48%, var(--stage-centre) 0%, var(--stage-edge) 78%);
    font-family: "Questrial", "Century Gothic", sans-serif;
  }
  .card {
    position: absolute;
    top: 468px;
    width: 499px;
    height: 277px;
    overflow: hidden;
    box-shadow: 0 10px 18px rgba(0, 0, 0, 0.28);
  }
  .card--front {
    left: 80px;
    background: linear-gradient(90deg, var(--card-dark) 0%, var(--card-dark-mid) 70%, #262626 100%);
  }
  .card--back {
    left: 609px;
    width: 498px;
    background: var(--card-light);
  }
  .front-glow {
    position: absolute;
    left: 200px;
    bottom: -30px;
    width: 300px;
    height: 60px;
    background: radial-gradient(ellipse at center, rgba(255,255,255,0.2), rgba(255,255,255,0) 70%);
  }
  .front-brand {
    position: absolute;
    left: 84px;
    top: 116px;
    display: flex;
    align-items: center;
    gap: 10px;
  }
  .brand-dot {
    width: 36px;
    height: 36px;
    border-radius: 50%;
    background: #f2f2f2;
  }
  .front-brand .wordmark {
    font-size: 34px;
    color: #ffffff;
    letter-spacing: 0.3px;
    line-height: 1;
  }
  .back-wordmark {
    position: absolute;
    left: 226px;
    top: 37px;
    font-size: 34px;
    color: var(--ink);
    line-height: 1;
    letter-spacing: 0.3px;
  }
  .person {
    position: absolute;
    left: 226px;
    top: 108px;
    font-family: "Cormorant SC", serif;
    font-weight: 600;
    letter-spacing: 2px;
    line-height: 14px;
  }
  .person__name { font-size: 13px; color: var(--ink-soft); }
  .person__role { font-size: 12px; color: var(--brand-green); }
  .address {
    position: absolute;
    left: 228px;
    top: 158px;
    font-size: 11px;
    letter-spacing: 1px;
    color: var(--ink-soft);
  }
  .contacts {
    position: absolute;
    left: 228px;
    top: 181px;
    margin: 0;
    padding: 0;
    list-style: none;
    font-size: 11px;
    letter-spacing: 1.2px;
    color: var(--ink-soft);
  }
  .contacts li {
    display: flex;
    align-items: center;
    height: 16.5px;
  }
  .contacts svg {
    width: 10px;
    height: 10px;
    margin-right: 14px;
    fill: none;
    stroke: var(--brand-blue);
    stroke-width: 1.4;
  }
  .back-band {
    position: absolute;
    right: 0;
    bottom: 0;
    width: 324px;
    height: 14px;
    background: var(--band-green);
    border-radius: 14px 0 0 0;
  }
</style>
</head>
<body>
  <section class="card card--front">
    <div class="front-glow"></div>
    <div class="front-brand">
      <span class="brand-dot"></span>
      <span class="wordmark">brovaLINK</span>
    </div>
  </section>

  <section class="card card--back">
    <div class="back-wordmark">brovaLINK</div>
    <div class="person">
      <div class="person__name">Lukas Brenner</div>
      <div class="person__role">CEO</div>
    </div>
    <div class="address">Lindenweg 8, 5400 Baden, Switzerland</div>
    <ul class="contacts">
      <li><svg viewBox="0 0 10 10"><path d="M1 4 Q5 0 9 4 M2 4 L2 8 L8 8 L8 4"/></svg>+41 56 000 12 34</li>
      <li><svg viewBox="0 0 10 10"><rect x="3" y="0.7" width="4" height="8.6" rx="0.8"/></svg>+41 79 000 56 78</li>
      <li><svg viewBox="0 0 10 10"><rect x="0.7" y="2" width="8.6" height="6"/><path d="M0.7 2 L5 5.5 L9.3 2"/></svg>lukas.brenner@brovalink.ch</li>
      <li><svg viewBox="0 0 10 10"><circle cx="5" cy="5" r="4.2"/><path d="M0.8 5 H9.2 M5 0.8 Q2.5 5 5 9.2 Q7.5 5 5 0.8"/></svg>www.brovalink.ch</li>
    </ul>
    <div class="back-band"></div>
  </section>
</body>
</html>
```